Brook Refrigeration. Refrigeration and air conditioning specialists.

We need a website to promote our business. We would a modern simple design using the colours from our logo and black. We want it to be fun but proffesional.

Target Market(s)

Commercial

Number of Pages Required

4 page

Requirements
Must have
• Home Page, About Us, Services and Contact Us.
• 24/7 365 days service available.
• Brook Refrigeration's dedicated team specialises in commercial refrigeration and air conditioning equipment.
• Based in Joondalup, we cover Perth Metro and surrounding areas.
Nice to have
• KNOWLEDGE . EXPERIENCE . PASSION in bold.
• Our experienced and highly trained technicians provide extensive knowledge and exceptional skills for your commercial refrigeration and air conditioning requirements.
• Pictures of commercial refrigeration.
Should not have
• No mention of domestic services.

```html
<!DOCTYPE html>
<html lang="en">
<head>
<meta charset="utf-8">
<title>Brook Refrigeration</title>
<link rel="stylesheet" href="https://fonts.googleapis.com/css2?family=Montserrat:wght@400;600;700;800&family=Roboto:wght@300;400;500;700&family=Roboto+Condensed:wght@400;700&display=swap">
<style>
:root{
  --lime:#a2ee6a;
  --lime-dark:#8ad655;
  --purple:#3d2458;
  --purple-nav:#3f2a5e;
  --ink:#2b2b2b;
  --muted:#6a6a6a;
  --footer:#333333;
  --white:#ffffff;
  --line:#c9c9c9;
}
*{margin:0;padding:0;box-sizing:border-box}
html,body{width:1200px;height:3629px;overflow:hidden}
body{position:relative;background:var(--white);font-family:'Roboto',sans-serif;color:var(--ink)}
.abs{position:absolute}

/* header */
.site-header{position:absolute;left:0;top:0;width:1200px;height:143px;background:var(--white)}
.brand{position:absolute;left:85px;top:28px;color:var(--lime);font-family:'Montserrat',sans-serif;font-weight:800;line-height:1}
.brand .name{font-size:58px;letter-spacing:1px;display:block}
.brand .sub{font-size:14px;letter-spacing:1px;display:block;margin-top:6px;padding-left:6px}
.service-badge{position:absolute;left:700px;top:28px;width:170px;text-align:center;color:var(--purple);font-family:'Montserrat',sans-serif}
.service-badge .clock{display:block;margin:0 auto 4px}
.service-badge .big{font-size:30px;font-weight:800}
.service-badge .days{font-size:18px;font-weight:700}
.service-badge .small{display:block;font-size:7px;letter-spacing:1px;margin-top:-2px;text-align:right;padding-right:12px}
.phone-tab{position:absolute;left:910px;top:0;width:290px;height:44px;background:var(--lime);border-radius:0 0 0 24px;display:flex;align-items:center;padding-left:22px;gap:10px;font-family:'Montserrat',sans-serif;font-weight:700;font-size:21px;color:var(--purple)}
.follow{position:absolute;left:945px;top:56px;width:150px;text-align:center;font-family:'Montserrat',sans-serif;font-weight:700;font-size:16px;color:var(--purple)}
.follow .social{display:flex;gap:3px;justify-content:center;margin-top:6px}
.follow .social span{width:18px;height:18px;background:var(--purple)}

/* nav */
.main-nav{position:absolute;left:0;top:143px;width:1200px;height:35px;background:var(--purple-nav);border-bottom:3px solid #2c1b42}
.main-nav a{position:absolute;top:0;height:32px;line-height:32px;width:200px;text-align:center;color:var(--white);text-decoration:none;font-size:14px;font-family:'Montserrat',sans-serif;border-right:1px solid #5a4778}
.main-nav a.active{background:var(--lime);color:var(--purple);width:137px}
.main-nav .search{position:absolute;left:925px;top:5px;width:185px;height:22px;background:var(--white);font-size:10px;color:#777;padding:5px 8px}
.main-nav .search svg{position:absolute;right:6px;top:5px}

/* hero */
.hero{position:absolute;left:0;top:178px;width:1200px;height:637px;background:linear-gradient(180deg,#5b5552 0%,#8d8781 35%,#6e6863 60%,#3f3a37 100%)}
.hero .copy{position:absolute;left:0;top:150px;width:1200px;text-align:center;color:var(--white)}
.hero .lead{font-family:'Montserrat',sans-serif;font-weight:400;font-size:44px}
.hero .title{font-family:'Roboto Condensed',sans-serif;font-weight:700;font-size:60px;line-height:72px;margin-top:8px;text-transform:uppercase}
.hero .values{font-family:'Montserrat',sans-serif;font-weight:700;font-size:42px;color:var(--lime);margin-top:4px}
.hero .btn{position:absolute;left:514px;top:443px;width:192px;height:44px;background:var(--lime);border-radius:4px;color:var(--purple);font-family:'Roboto Condensed',sans-serif;font-weight:700;font-size:22px;line-height:44px;text-align:center}
.hero .dots{position:absolute;left:578px;top:584px;display:flex;gap:10px}
.hero .dots span{width:9px;height:9px;border-radius:50%;border:2px solid var(--white)}
.hero .dots span.on{background:var(--white)}

/* about */
.about-photo{position:absolute;left:170px;top:935px;width:348px;height:435px;background:linear-gradient(160deg,#c9c2b5,#5b6d8d 60%,#2e3c5c);border:1px solid #999}
.about-text{position:absolute;left:595px;top:925px;width:450px}
.section-title{font-family:'Montserrat',sans-serif;font-weight:700;color:var(--purple)}
.about-text h2{font-size:34px}
.about-text .rule{width:70px;height:2px;background:var(--purple);margin:8px 0 30px}
.about-text p{font-size:12px;line-height:19px;color:var(--muted);margin-bottom:19px;font-weight:300}

/* services */
.services{position:absolute;left:0;top:1495px;width:1200px;height:970px;background:var(--purple)}
.services h2{position:absolute;top:72px;width:1200px;text-align:center;color:var(--lime);font-size:32px}
.services .intro{position:absolute;top:156px;left:120px;width:960px;text-align:center;color:#d8cfe5;font-size:12.5px;line-height:23px;font-weight:300}
.card{position:absolute;width:283px;height:269px;background:var(--lime);border-radius:10px}
.card .photo{position:absolute;left:9px;top:9px;width:265px;height:195px;border-radius:8px}
.card .label{position:absolute;left:0;top:216px;width:283px;text-align:center;font-family:'Montserrat',sans-serif;font-weight:700;font-size:18px;color:var(--ink)}
.arrow{position:absolute;top:490px}

/* contact */
.contact h2{position:absolute;top:2555px;width:1200px;text-align:center;font-size:32px}
.contact .rule{position:absolute;left:565px;top:2610px;width:70px;height:2px;background:var(--line)}
.field-label{position:absolute;font-size:13px;color:var(--ink)}
.field-label b{color:#c0392b;font-weight:400;margin-left:6px}
.field{position:absolute;border:1px solid #bdbdbd;background:var(--white)}
.note{position:absolute;font-size:12px;color:var(--muted)}
.submit{position:absolute;left:532px;top:2962px;width:136px;height:38px;background:var(--purple);color:var(--white);font-family:'Montserrat',sans-serif;font-weight:700;font-size:16px;line-height:38px;text-align:center;border-radius:3px}

/* newsletter */
.newsletter{position:absolute;left:0;top:3085px;width:1200px;height:150px;background:var(--lime)}
.newsletter .label{position:absolute;left:172px;top:57px;font-family:'Montserrat',sans-serif;font-weight:700;font-size:22px;color:var(--purple)}
.newsletter .input{position:absolute;left:382px;top:50px;width:506px;height:50px;background:var(--white)}
.newsletter .btn{position:absolute;left:888px;top:50px;width:128px;height:50px;background:var(--purple);color:var(--white);font-family:'Montserrat',sans-serif;font-weight:700;font-size:13px;line-height:50px;text-align:center}

/* footer */
.site-footer{position:absolute;left:0;top:3235px;width:1200px;height:320px;background:var(--footer);color:var(--white)}
.site-footer .brand{left:110px;top:100px;color:var(--white)}
.site-footer .brand .name{font-size:60px}
.site-footer h4{position:absolute;top:65px;font-family:'Montserrat',sans-serif;font-weight:700;font-size:16px;color:var(--lime)}
.site-footer .info{position:absolute;font-size:13px;line-height:18px}
.site-footer .info .k{color:var(--lime);font-weight:700;font-family:'Montserrat',sans-serif;font-size:13px}
.site-footer .links{position:absolute;left:628px;top:117px;list-style:none;font-size:14px;line-height:33px}
.site-footer .fin{position:absolute;height:36px;background:var(--white);font-size:12px;color:#888;padding:11px 10px}
.site-footer .send{position:absolute;left:792px;top:202px;width:134px;height:38px;background:var(--lime);color:var(--purple);font-family:'Montserrat',sans-serif;font-weight:700;font-size:15px;line-height:38px;text-align:center}
.copyright{position:absolute;left:0;top:3555px;width:1200px;height:74px;background:var(--purple);color:#d8cfe5;font-size:12px;text-align:center;line-height:74px}
</style>
</head>
<body>

<header class="site-header">
  <div class="brand"><span class="name">BROOK</span><span class="sub">REFRIGERATION</span></div>
  <div class="service-badge">
    <svg class="clock" width="44" height="44" viewBox="0 0 44 44"><circle cx="22" cy="22" r="20" fill="var(--purple)"/><circle cx="22" cy="22" r="13" fill="none" stroke="#fff" stroke-width="2"/><path d="M22 14v8l6 4" stroke="#fff" stroke-width="2" fill="none"/></svg>
    <span class="big">24/7</span> <span class="days">365 DAYS</span>
    <span class="small">SERVICE AVAILABLE</span>
  </div>
  <div class="phone-tab">
    <svg width="22" height="26" viewBox="0 0 22 26"><rect x="3" y="1" width="16" height="24" rx="3" fill="none" stroke="var(--purple)" stroke-width="2.5"/><circle cx="11" cy="20" r="1.6" fill="var(--purple)"/></svg>
    1-800-555-0142
  </div>
  <div class="follow">Follow Us
    <div class="social"><span></span><span></span><span></span><span></span><span></span><span></span></div>
  </div>
</header>

<nav class="main-nav">
  <a class="active" style="left:85px">Home</a>
  <a style="left:222px">About Us</a>
  <a style="left:422px">Services</a>
  <a style="left:622px">Contact Us</a>
  <div class="search">Search
    <svg width="12" height="12" viewBox="0 0 12 12"><circle cx="5" cy="5" r="3.5" fill="none" stroke="#555" stroke-width="1.5"/><path d="M7.5 7.5l3.5 3.5" stroke="#555" stroke-width="1.5"/></svg>
  </div>
</nav>

<section class="hero" role="img" aria-label="Photo of silver ductwork and refrigeration piping on a ceiling">
  <div class="copy">
    <div class="lead">Our dedicated team specialises in</div>
    <div class="title">Commercial Refrigeration &amp;<br>Air Conditioning Equipment.</div>
    <div class="values">KNOWLEDGE • EXPERIENCE • PASSION</div>
  </div>
  <div class="btn">KNOW MORE</div>
  <div class="dots"><span class="on"></span><span></span><span></span></div>
</section>

<section class="about">
  <div class="about-photo" role="img" aria-label="Photo of a smiling refrigeration technician in a blue cap holding a clipboard"></div>
  <div class="about-text">
    <h2 class="section-title">About us</h2>
    <div class="rule"></div>
    <p>Brook Refrigeration's dedicated team specialises in commercial refrigeration and air conditioning equipment. Based in Joondalup, we cover Perth Metro and surrounding areas.</p>
    <p>Our experienced and highly trained technicians provide extensive knowledge and exceptional skills for your commercial refrigeration and air conditioning requirements. From the first call to the final check, we work quickly and carefully, keeping your cool rooms, display cases and freezers running at the right temperature so your stock stays fresh and your business keeps moving through every season.</p>
    <p>We service, repair and install equipment for cafes, restaurants, bakeries and supermarkets across the region. Our vans carry common parts, so most faults are fixed on the first visit, and our team is on call day and night whenever you need us.</p>
  </div>
</section>

<section class="services">
  <h2 class="section-title">Our Services</h2>
  <div class="intro">Whether you wish to cool, store or display food and drink, we have a wide range of commercial refrigerator services catering to various small and large scale industries.<br>We specialize in wide range of commercial refrigeration operations and maintenance services to ensure efficient functioning of the systems.</div>

  <svg class="arrow" style="left:55px" width="26" height="50" viewBox="0 0 26 50"><path d="M22 2L4 25l18 23" fill="none" stroke="#8d7fa6" stroke-width="2"/></svg>
  <svg class="arrow" style="left:1118px" width="26" height="50" viewBox="0 0 26 50"><path d="M4 2l18 23L4 48" fill="none" stroke="#8d7fa6" stroke-width="2"/></svg>

  <div class="card" style="left:133px;top:252px"><div class="photo" role="img" aria-label="Photo of a chest freezer with an open lid" style="background:linear-gradient(180deg,#fff,#dfe4ea)"></div><div class="label">Commercial Freezer</div></div>
  <div class="card" style="left:460px;top:252px"><div class="photo" role="img" aria-label="Photo of a walk-in cooler room" style="background:linear-gradient(180deg,#fff,#cfd2d6)"></div><div class="label">Walk In Cooler</div></div>
  <div class="card" style="left:791px;top:252px"><div class="photo" role="img" aria-label="Photo of a stainless steel kitchen refrigerator" style="background:linear-gradient(180deg,#fff,#c6c9cd)"></div><div class="label">Kitchen Refrigeration</div></div>
  <div class="card" style="left:133px;top:589px"><div class="photo" role="img" aria-label="Photo of a glass door drinks merchandiser" style="background:linear-gradient(180deg,#fff,#5b6a7d)"></div><div class="label">Glass Door Merchandiser</div></div>
  <div class="card" style="left:460px;top:589px"><div class="photo" role="img" aria-label="Photo of a curved glass bakery display case" style="background:linear-gradient(180deg,#fff,#6b5a4f)"></div><div class="label">Bakery Display Case</div></div>
  <div class="card" style="left:791px;top:589px"><div class="photo" role="img" aria-label="Photo of a stainless steel ice machine" style="background:linear-gradient(180deg,#fff,#bfc3c8)"></div><div class="label">Ice machines</div></div>
</section>

<section class="contact">
  <h2 class="section-title">Contact Us</h2>
  <div class="rule"></div>
  <div class="field-label" style="left:152px;top:2668px">Name<b>*</b></div>
  <div class="field" style="left:152px;top:2692px;width:396px;height:38px"></div>
  <div class="field-label" style="left:152px;top:2752px">Email<b>*</b></div>
  <div class="field" style="left:152px;top:2777px;width:396px;height:38px"></div>
  <div class="field-label" style="left:152px;top:2838px">Phone</div>
  <div class="field" style="left:152px;top:2862px;width:396px;height:38px"></div>
  <div class="field-label" style="left:673px;top:2668px">Description</div>
  <div class="field" style="left:673px;top:2692px;width:397px;height:133px"></div>
  <div class="note" style="left:673px;top:2838px"><span style="color:#c0392b">*</span> Required</div>
  <div class="field" style="left:675px;top:2876px;width:14px;height:14px"></div>
  <div class="note" style="left:698px;top:2876px">I have read the Disclaimer and Privacy Policy</div>
  <div class="submit">SUBMIT</div>
</section>

<section class="newsletter">
  <div class="label">NEWSLETTER</div>
  <div class="input"></div>
  <div class="btn">SUBSCRIBE</div>
</section>

<footer class="site-footer">
  <div class="brand"><span class="name">BROOK</span><span class="sub">REFRIGERATION</span></div>
  <h4 style="left:358px">CONTACT US</h4>
  <svg class="abs" style="left:352px;top:106px" width="22" height="30" viewBox="0 0 22 30"><path d="M11 1C5.5 1 1.5 5 1.5 10.5 1.5 18 11 29 11 29s9.5-11 9.5-18.5C20.5 5 16.5 1 11 1z" fill="var(--lime)"/><circle cx="11" cy="10.5" r="3.8" fill="var(--footer)"/></svg>
  <div class="info" style="left:393px;top:104px"><span class="k">ADDRESS</span><br>42 Harbourview Lane<br>Joondalup WA 6027</div>
  <svg class="abs" style="left:354px;top:188px" width="22" height="22" viewBox="0 0 22 22"><path d="M5 1l4 5-2.5 2.5c1.5 3 4 5.5 7 7L16 13l5 4-2.5 4C9 21 1 13 1 3.5z" fill="var(--lime)"/></svg>
  <div class="info" style="left:393px;top:188px"><span class="k" style="color:#fff">PHONE NUMBER</span><br><b>1-800-555-0142</b></div>
  <h4 style="left:625px">ABOUT</h4>
  <ul class="links"><li>Home</li><li>About Us</li><li>Services</li><li>Contact us</li></ul>
  <h4 style="left:790px">GET IN TOUCH</h4>
  <div class="fin" style="left:792px;top:111px;width:153px">Name</div>
  <div class="fin" style="left:950px;top:111px;width:153px">Phone</div>
  <div class="fin" style="left:792px;top:155px;width:311px">Email address</div>
  <div class="send">SEND</div>
</footer>

<div class="copyright">© 2018 brookrefrigeration All Right Reserved</div>

</body>
</html>
```